Business Cards for a law firm

Business cards for our law firm. Use our silhoette logo and OAK PARTNERS - check our website (www.oakpartners.example)

Contact Information for Business Card

our silhouette logo, OAK PARTNERS, 800-555-0147, Dorian Pemberton, dorian@oakpartners.example

Requirements
Must have
• our silhouette logo, OAK PARTNERS, 800-555-0147, Dorian Pemberton, dorian@oakpartners.example

```html
<!DOCTYPE html>
<html lang="en">
<head>
<meta charset="utf-8">
<title>Oak Partners Business Cards</title>
<link rel="stylesheet" href="https://fonts.googleapis.com/css2?family=Montserrat:wght@400;500;600;700&display=swap">
<style>
  :root {
    --navy: #1f2c6b;
    --navy-deep: #18225a;
    --navy-light: #3a4c9c;
    --paper: #ffffff;
    --paper-shade: #f1f2f5;
    --backdrop: #d9dce2;
    --ink-soft: #4a4f63;
  }
  * { box-sizing: border-box; margin: 0; padding: 0; }
  html, body {
    width: 1200px; height: 900px; overflow: hidden;
    background: var(--backdrop);
    font-family: "Montserrat", sans-serif;
  }
  .canvas { position: relative; width: 1200px; height: 900px; }

  .card {
    position: absolute;
    width: 560px; height: 320px;
    box-shadow: 0 6px 18px rgba(20, 25, 50, .22);
    overflow: hidden;
  }

  /* Back of card */
  .card-back { left: 80px; top: 90px; background: var(--navy); }
  .back-pattern {
    position: absolute; inset: 0;
    background: linear-gradient(135deg, var(--navy-light) 0%, var(--navy) 45%, var(--navy-deep) 100%);
  }
  .back-brand {
    position: absolute; left: 0; right: 0; top: 140px;
    display: flex; align-items: center; justify-content: center; gap: 14px;
    color: var(--paper);
  }
  .brand-mark { width: 22px; height: 22px; background: currentColor; }
  .back-brand .brand-name {
    font-size: 26px; font-weight: 500; letter-spacing: 4px;
  }

  /* Front of card */
  .card-front {
    left: 560px; top: 480px;
    background: linear-gradient(180deg, var(--paper-shade) 0%, var(--paper) 35%);
  }
  .front-brand {
    position: absolute; left: 40px; top: 44px;
    display: flex; align-items: center; gap: 18px;
    color: var(--navy);
  }
  .front-brand .brand-mark { width: 34px; height: 34px; }
  .front-brand .brand-name {
    font-size: 38px; font-weight: 600; letter-spacing: 5px;
  }

  .holder {
    position: absolute; left: 60px; top: 150px; width: 200px;
    text-align: right; color: var(--navy);
  }
  .holder-name { font-size: 20px; font-weight: 700; }
  .holder-title { font-size: 12px; color: var(--ink-soft); margin-top: 2px; }

  .divider {
    position: absolute; left: 278px; top: 140px;
    width: 1px; height: 62px; background: var(--navy);
  }

  .contact-list {
    position: absolute; left: 294px; top: 140px;
    list-style: none; color: var(--ink-soft); font-size: 12.5px;
  }
  .contact-list li { display: flex; align-items: center; gap: 8px; height: 21px; }
  .contact-list svg { width: 12px; height: 12px; fill: var(--navy); flex: none; }

  .address-band {
    position: absolute; left: 0; right: 0; bottom: 36px; height: 40px;
    background: var(--navy); color: var(--paper);
    display: flex; align-items: center; justify-content: center;
    font-size: 13px; letter-spacing: .3px;
  }
</style>
</head>
<body>
<main class="canvas">

  <section class="card card-back">
    <div class="back-pattern" role="img" aria-label="Repeating pattern of brand silhouettes in tones of navy blue"></div>
    <div class="back-brand">
      <span class="brand-mark"></span>
      <span class="brand-name">OAK PARTNERS</span>
    </div>
  </section>

  <section class="card card-front">
    <div class="front-brand">
      <span class="brand-mark"></span>
      <span class="brand-name">OAK PARTNERS</span>
    </div>

    <div class="holder">
      <p class="holder-name">Dorian Pemberton</p>
      <p class="holder-title">Lawyer</p>
    </div>

    <div class="divider"></div>

    <ul class="contact-list">
      <li>
        <svg viewBox="0 0 24 24"><path d="M6.6 10.8a15 15 0 0 0 6.6 6.6l2.2-2.2a1 1 0 0 1 1-.25 11.4 11.4 0 0 0 3.6.57 1 1 0 0 1 1 1V20a1 1 0 0 1-1 1A17 17 0 0 1 3 4a1 1 0 0 1 1-1h3.5a1 1 0 0 1 1 1c0 1.25.2 2.45.57 3.6a1 1 0 0 1-.25 1z"/></svg>
        <span>800-555-0147</span>
      </li>
      <li>
        <svg viewBox="0 0 24 24"><path d="M2 5h20v2l-10 6L2 7zM2 9.3l10 6 10-6V19H2z"/></svg>
        <span>dorian@oakpartners.example</span>
      </li>
      <li>
        <svg viewBox="0 0 24 24"><path d="M12 2a10 10 0 1 0 0 20 10 10 0 0 0 0-20zm0 2c.9 0 2.2 2 2.7 5H9.3C9.8 6 11.1 4 12 4zM4.3 11h3a17 17 0 0 0 0 2h-3a8 8 0 0 1 0-2zm5 0h5.4a15 15 0 0 1 0 2H9.3a15 15 0 0 1 0-2zm7.4 0h3a8 8 0 0 1 0 2h-3a17 17 0 0 0 0-2zM9.3 15h5.4c-.5 3-1.8 5-2.7 5s-2.2-2-2.7-5z"/></svg>
        <span>www.oakpartners.example</span>
      </li>
    </ul>

    <div class="address-band">418 Maple Crest Ave, #112 Fairview, OH 430571</div>
  </section>

</main>
</body>
</html>
```